New Business Card for Web Design/Internet Marketing Company

Looking for a great looking new business card. We are a 10 year old web design, internet marketing and website management company that works mostly with small businesses.

Our new card needs to better match the colors and style of our website, be bold, extremely usable and slightly edgy.

Target Market(s)

Small/Medium businesses that have websites

Industry/Entity Type

Internet

Requirements
Must have
• Front and back design, full color, rounded corners please

Must use the colors/style of our website (JPG provided)

INFO FOR CARDS (as readable as possible please)
Mark Lenner
President/CEO
mark@trelvanmedia.example
Phone: 520-381-7459
Toll Free: 866-381-7459
Address: 4315 W. Calloway Ave. Ste. 140, Tucson, AZ 85792

THINGS I WANT TO PROMOTE (if there is room):
1. Our Website - www.trelvanmedia.example

2. Social Media
Chirply: @trelvanmedia
Friendspace: www.facebook.com/trelvanmedia

3. Our Services
Web Design
Internet Marketing
Website Management

```html
<!DOCTYPE html>
<html lang="en">
<head>
<meta charset="utf-8">
<title>Trelvan Media – Business Card</title>
<link rel="stylesheet" href="https://fonts.googleapis.com/css2?family=Open+Sans:ital,wght@0,400;0,600;0,700;1,400&display=swap">
<style>
  :root {
    --blue: #1b86c2;
    --orange: #ee7b22;
    --ink: #3a3a3a;
    --white: #ffffff;
    --backdrop: #e6e7e9;
  }
  * { box-sizing: border-box; margin: 0; padding: 0; }
  html, body {
    width: 1200px; height: 944px; overflow: hidden;
    background: var(--backdrop);
    font-family: "Open Sans", Arial, sans-serif;
    color: var(--ink);
  }
  .canvas { position: relative; width: 1200px; height: 944px; }

  .card {
    position: absolute;
    width: 540px; height: 309px;
    border-radius: 26px;
    overflow: hidden;
    background: var(--white);
    box-shadow: 0 6px 18px rgba(0,0,0,0.18);
  }
  .card--front { left: 70px; top: 110px; }
  .card--back  { left: 590px; top: 520px; }

  /* brand lockup */
  .brand { display: flex; align-items: center; gap: 14px; }
  .brand__dot {
    width: 40px; height: 40px; border-radius: 50%;
    background: var(--orange); flex: none;
  }
  .brand__name {
    font-weight: 700; font-size: 46px; line-height: 1;
    color: var(--blue); letter-spacing: -0.5px; white-space: nowrap;
  }
  .brand__tagline {
    font-size: 15px; color: var(--ink); font-weight: 600;
    margin-top: 6px; text-align: right;
  }

  /* front */
  .front__brand { position: absolute; left: 74px; top: 78px; }
  .front__web {
    position: absolute; left: 0; right: 0; top: 216px;
    text-align: center; font-size: 15px; font-weight: 600;
    color: var(--ink); letter-spacing: 0.3px;
  }
  .front__band {
    position: absolute; left: 0; right: 0; bottom: 0; height: 54px;
    background: var(--blue);
    display: flex; align-items: center; justify-content: center; gap: 10px;
    color: var(--white); font-size: 15.5px; font-weight: 600;
  }
  .front__band .sep { font-size: 12px; }

  /* back */
  .back__brand { position: absolute; left: 74px; top: 34px; }
  .back__rule {
    position: absolute; left: 0; right: 0; top: 126px; height: 6px;
    background: var(--orange);
  }
  .back__panel {
    position: absolute; left: 0; right: 0; top: 132px; bottom: 0;
    background: var(--blue);
    color: var(--white);
    padding: 18px 28px 0 0;
    font-size: 14px; line-height: 1.45;
    text-align: right;
  }
  .person { margin-bottom: 6px; }
  .person__name { color: var(--orange); font-size: 19px; font-weight: 600; }
  .person__title { font-size: 14px; font-style: italic; margin-left: 4px; }
  .accent { color: var(--orange); }
  .contact-row { white-space: nowrap; }
  .contact-row > span + span { margin-left: 16px; }
</style>
</head>
<body>
<main class="canvas">

  <section class="card card--front" aria-label="Card front">
    <div class="front__brand">
      <div class="brand">
        <span class="brand__dot"></span>
        <span class="brand__name">Trelvan Media</span>
      </div>
      <p class="brand__tagline">Grow your Business</p>
    </div>
    <p class="front__web">www.trelvanmedia.example</p>
    <div class="front__band">
      <span>Web Design</span><span class="sep">●</span>
      <span>Internet Marketing</span><span class="sep">●</span>
      <span>Website Management</span>
    </div>
  </section>

  <section class="card card--back" aria-label="Card back">
    <div class="back__brand">
      <div class="brand">
        <span class="brand__dot"></span>
        <span class="brand__name">Trelvan Media</span>
      </div>
      <p class="brand__tagline">Grow your Business</p>
    </div>
    <div class="back__rule"></div>
    <div class="back__panel">
      <p class="person">
        <span class="person__name">Mark Lenner</span>
        <span class="person__title">President/CEO</span>
      </p>
      <p>mark@trelvanmedia.example</p>
      <p class="contact-row"><span>Phone: 520-381-7459</span><span>Toll Free: 866-381-7459</span></p>
      <p class="contact-row"><span><span class="accent">Chirply</span>@trelvanmedia</span><span><span class="accent">www.friendspace.example</span>/trelvanmedia</span></p>
      <p class="contact-row">4315 W. Calloway Ave. Ste. 140 Tucson, AZ 85792</p>
    </div>
  </section>

</main>
</body>
</html>
```